Power Point Template Vierklang sustainability consulting

(find english description below)
We are a small German start-up that offers sustainability consulting. For presentations of results, our company presentation, proposals, lectures, etc., we need a PowerPoint template that matches our logo. We come from classic management consulting / strategy consulting and also deal with facts and figures in sustainability consulting. Therefore, the template should not be too fancy and should not only consist of photos. But it shouldn't be a completely sober template either. Our logo with the green leaves for sustainability (three leaves for VIERklang) and the white bar chart (with the dynamic swing upwards) reflects our attitude well, where we see ourselves on the range from playful to sober and classic to modern.

It might be nice for the template to include the shape of one of the leaves (from the logo). Also, the logo should appear in a corner of each slide. The colors from the logo (see appendix) should be partially reflected in the presentation. We can also imagine a gold-brown tone (see website www.vierklang-beratung.de) or a coral tone as a contrast. (Attention - the website is not final yet).

For a first suggestion, it is sufficient to suggest three to four slides (cover sheet, chapter/separation slide, text slide, data slide). We will then mark drafts that we like. In total, we would then need about 6-10 more slide templates, e.g. about us, team, slide for a statement, 2-3 data charts (pie, bar, column), top 3 - 5 list, timeline, contact (more slides are welcome ).

We are a small German start-up offering sustainability consulting. We need a power point template for result presentations, our company presentation, proposals, lectures etc. The template should be aligned with our logo. Our background lies in classic management consulting / strategy consulting and we also deal with facts and figures in sustainability consulting. Therefore, the template should not be too playful and not only consist of photos. But it should also not be a completely clear template. Our logo with the green leaves for sustainability (three leaves for VIERklang) and the white bar chart (with the dynamic upward swing) reflects our attitude well, where we see ourselves on the range from playful to down-to-earth and classic to modern .

For the template, it might be nice to incorporate the shape of one of the leaves (from the logo). Also, the logo should show up in one corner on each slide. Some of the colors from the logo (see attachment) should be reflected in the presentation. We could also think of a gold-brown tone (see website www.vierklang-beratung.de) or a coral tone for contrast. (Attention - the website is not final yet).

For a first proposal it is quite sufficient to suggest us three to four slides (cover page, chapter/separation slide, text slide, data slide). We will then mark the drafts that we like. In total we would need about 6-10 more slide templates, eg About us, Team, slide for a statement, 2-3 data charts (pie, bar, column), Top 3 - 5 List, Timeline, Contact (more slides are welcome).

Target Market(s)

Corporations, large companies and SMEs

Industry/Entity Type

Unternehmensberatung, Nachhaltigkeitsberatung

Font styles to use
Sans Serif
Other font styles liked:
• Calibri

Colors
00AB8E
00BBA5
67D7C9
C6EFE9
E9F9F6

Requirements
Must have
• see description (e.g. the colors of our logo)
Nice to have
• see description (e.g. elements of the logo included)
Should not have
• see description

```html
<!DOCTYPE html>
<html lang="de">
<head>
<meta charset="utf-8">
<title>Vierklang – Präsentationsvorlage</title>
<link href="https://fonts.googleapis.com/css2?family=Cabin:wght@400;500;600&display=swap" rel="stylesheet">
<style>
:root{
  --bg:#c8c8c8;
  --ink:#3a2f14;
  --gold:#c9ab70;
  --gold-dark:#8a6a22;
  --sand:#dccba0;
  --sand-light:#efe6cc;
  --green:#7fb23a;
  --green-mid:#a8c94a;
  --green-light:#cfdf7a;
  --green-dark:#4f7d1c;
  --white:#ffffff;
}
*{box-sizing:border-box;margin:0;padding:0}
html,body{width:1200px;height:972px;overflow:hidden}
body{background:var(--bg);font-family:"Cabin",sans-serif;font-weight:400;color:var(--ink);position:relative}
b{font-weight:600}
.slide{position:absolute;width:368px;height:207px;background:var(--white);overflow:hidden;box-shadow:0 1px 3px rgba(0,0,0,.15)}
.abs{position:absolute}
.c1{left:31px}.c2{left:418px}.c3{left:805px}
.r1{top:32px}.r2{top:262px}.r3{top:492px}.r4{top:713px}
.brand{position:absolute;display:flex;align-items:center;gap:4px;color:var(--green);font-weight:500}
.brand i{display:block;border-radius:50%;background:var(--green)}
.foot{position:absolute;left:0;bottom:0;width:100%;height:16px;background:var(--sand)}
.foot .url{position:absolute;left:17px;top:4px;font-size:6.5px;color:var(--ink)}
.foot .brand{right:8px;top:3px;font-size:7px}
.foot .brand i{width:7px;height:7px}
.title{font-size:13px;letter-spacing:.2px;font-weight:400}
.photo{position:absolute}
/* toc */
.toc-item{position:absolute;left:176px;display:flex;align-items:center;gap:5px;font-size:9px}
.toc-item b{width:15px;height:15px;border-radius:50%;border:1.3px solid var(--gold);background:var(--white);font-size:7.5px;font-weight:400;display:flex;align-items:center;justify-content:center}
/* cards */
.card{position:absolute;border:1.2px solid var(--sand-light);border-radius:8px;text-align:center}
.card h4{font-size:5.5px;font-weight:400;color:var(--gold);margin-top:44px;line-height:7px}
.card p{font-size:4.3px;line-height:5.6px;padding:0 8px;margin-top:5px}
.card ul{list-style:none;text-align:left;padding-left:12px;margin-top:5px;font-size:4.3px;line-height:5px}
.card li{display:flex;align-items:flex-start;gap:3px;margin-bottom:3px}
.card li::before{content:"";flex:none;width:5px;height:5px;border-radius:50%;background:var(--sand);margin-top:-.5px}
.avatar{position:absolute;width:70px;height:70px;border-radius:50%;border:5px solid var(--sand-light)}
/* services */
.svc{position:absolute;width:72px;text-align:center}
.svc h5{font-size:6px;font-weight:400;color:var(--ink)}
.svc p{font-size:4.5px;line-height:5.6px;margin-top:1px}
.tick-list{position:absolute;font-size:4.2px;line-height:5.6px;list-style:none}
.tick-list .lb{color:var(--gold-dark);margin-bottom:1px}
.tick-list li.t::before{content:"✓ ";color:var(--green)}
/* understanding */
.ucard{position:absolute;top:35px;width:94px;height:125px;border:1.5px solid var(--green-light);border-radius:7px;text-align:center}
.ucard.mid{border-color:var(--green)}
.ucard h4{font-size:8.5px;font-weight:400;color:var(--green-mid);line-height:11px;margin-top:8px}
.ucard p{font-size:4.8px;line-height:6.2px;padding:0 8px;margin-top:7px}
.pill{position:absolute;left:50%;bottom:-8px;transform:translateX(-50%);background:var(--white);border:1.5px solid var(--sand);border-radius:8px;font-size:5.3px;padding:3px 7px;white-space:nowrap}
.ucard.mid .pill{border-color:var(--ink)}
/* timeline */
.tl{position:absolute;width:60px;text-align:center;top:131px}
.tl .y{font-size:9.5px}
.tl .h{font-size:6.5px;color:#6b5a35}
.tl .d{font-size:4.3px;line-height:5.5px;margin-top:1px}
/* data */
.dh{position:absolute;font-size:10px;color:var(--gold)}
.dp{position:absolute;font-size:6.3px;line-height:8.6px;width:92px;color:#6b5a35}
/* contact */
.ct{position:absolute;left:21px;display:flex;gap:6px;font-size:6.3px;line-height:8.3px;align-items:flex-start}
.ct svg{flex:none;margin-top:1px}
</style>
</head>
<body>

<section class="slide c1 r1">
  <div class="brand" style="left:13px;top:18px;font-size:12px"><i style="width:10px;height:10px"></i>Vierklang</div>
  <div class="abs title" style="left:13px;top:106px">TITLE OF THE PRESENTATION</div>
</section>

<section class="slide c2 r1">
  <div class="photo" role="img" aria-label="Foto: Person sitzt am Steg vor einem Bergsee" style="left:0;top:0;width:368px;height:155px;background:linear-gradient(180deg,#d9dcaa 0%,#c4c98f 55%,#b6b880 100%)"></div>
  <div class="abs title" style="left:19px;top:81px">TITLE OF THE PRESENTATION</div>
  <svg class="abs" style="left:24px;top:154px" width="16" height="10"><path d="M0 0 L16 0 L8 10Z" fill="#b6b880"/></svg>
  <div class="brand" style="left:38px;top:172px;font-size:11px"><i style="width:9px;height:9px"></i>Vierklang</div>
  <div class="abs" style="right:17px;top:179px;font-size:6.3px">www.vierklang-beratung.de</div>
</section>

<section class="slide c3 r1">
  <div class="photo" role="img" aria-label="Foto: Weizenähren im Gegenlicht" style="left:13px;top:11px;width:342px;height:184px;background:linear-gradient(120deg,#c9b888 0%,#d9c58e 45%,#e6d3a0 75%,#d8c08a 100%)"></div>
  <div class="abs" style="right:25px;top:80px;text-align:right;font-size:22px;line-height:30px;color:var(--ink)">WIR SEHEN<br>NACHHALTIGKEIT<br>ALS CHANCE</div>
  <div class="abs" style="right:25px;top:170px;width:144px;height:2px;background:var(--ink)"></div>
</section>

<section class="slide c1 r2">
  <div class="photo" role="img" aria-label="Foto: Feldweg in goldener Abendlandschaft" style="left:0;top:0;width:184px;height:207px;background:linear-gradient(160deg,#d6c486 0%,#cbb878 50%,#c2ad73 100%)"></div>
  <div class="abs" style="left:20px;top:87px;font-size:12.5px">INHALTSVERZEICHNIS</div>
  <div class="abs" style="left:20px;top:104px;width:110px;height:2.5px;background:var(--ink)"></div>
  <div class="toc-item" style="top:24px"><b>01</b>Über Vierklang</div>
  <div class="toc-item" style="top:57px"><b>02</b>Wir verstehen</div>
  <div class="toc-item" style="top:89px"><b>03</b>Wir sind</div>
  <div class="toc-item" style="top:121px"><b>04</b>Über Nachhaltigkeit</div>
  <div class="toc-item" style="top:153px"><b>05</b>Sie möchten mehr erfahren?</div>
</section>

<section class="slide c2 r2">
  <div class="abs" style="left:18px;top:30px;font-size:15px;color:var(--gold)">WIR SIND...</div>
  <p class="abs" style="left:18px;top:62px;width:160px;font-size:7.2px;line-height:13.1px">drei Beraterinnen, für die NACHHALTIGKEIT bei einem Nachhaltigkeitsbericht nicht endet. Wir sehen die Umsetzung nachhaltiger Strategien als eine ganzheitliche und langfristige unternehmerische Entscheidung in die Zukunft für mehr Erfolg, mehr Stabilität und mehr Zufriedenheit – für Kunden, Geschäftspartner wie auch Mitarbeitende.</p>
  <div class="abs" style="left:197px;top:33px;width:140px;height:140px;border-radius:50%;border:2.5px solid var(--green-mid);padding:4px">
    <div role="img" aria-label="Teamfoto der drei Beraterinnen" style="width:100%;height:100%;border-radius:50%;background:linear-gradient(180deg,#b8c99a 0%,#8fa27a 50%,#2f3440 100%)"></div>
  </div>
  <div class="foot"><span class="url">www.vierklang-beratung.de</span><span class="brand"><i></i>Vierklang</span></div>
</section>

<section class="slide c3 r2">
  <div class="card" style="left:16px;top:60px;width:101px;height:121px">
    <h4>UNSERE ARBEITSWEISE</h4>
    <p>Uns Drei von Vierklang verbindet langjähriges gemeinsames Arbeiten. Wir arbeiten</p>
    <ul><li>Praxisnah &amp; interdisziplinär</li><li>Faktenbasiert &amp; wissenschaftlich fundiert</li><li>Pragmatisch &amp; lösungsorientiert</li><li>Leidenschaftlich &amp; kreativ</li></ul>
  </div>
  <div class="card" style="left:133px;top:60px;width:101px;height:121px">
    <h4>UNSERE ERFAHRUNG</h4>
    <p>Wir sind promovierte Betriebs- und Volkswirtinnen mit quantitativem Schwerpunkt. Wir können jeweils auf 10 bis 15 Jahre Erfahrung in der Unternehmensberatung, in der Marktforschung und im Projektmanagement zurückgreifen, mit Konzernen, KMUs und öffentlichen Einrichtungen.</p>
  </div>
  <div class="card" style="left:251px;top:60px;width:101px;height:121px">
    <h4 style="margin-top:42px">UNSER HINTERGRUND ZUR NACHHALTIGKEIT</h4>
    <p>Ausbildung zum Berichtsstandard – Certified Sustainable Professional</p>
    <p>Ausbildung zur Nachhaltigkeitsmanagerin nach ISO 26000</p>
    <p>Partnerin eines Nachhaltigkeitsinstituts – Beratung für nachhaltigen Wandel</p>
  </div>
  <div class="avatar" role="img" aria-label="Foto: drei Beraterinnen" style="left:31px;top:22px;background:linear-gradient(180deg,#c9ccc8,#4a4c55)"></div>
  <div class="avatar" role="img" aria-label="Foto: Beraterin am Laptop" style="left:148px;top:22px;background:linear-gradient(180deg,#dfe3e8,#5b6170)"></div>
  <div class="avatar" role="img" aria-label="Foto: Hände mit Unterlagen" style="left:266px;top:22px;background:linear-gradient(180deg,#eceef1,#b9bdc6)"></div>
  <div class="foot"><span class="url">www.vierklang-beratung.de</span><span class="brand"><i></i>Vierklang</span></div>
</section>

<section class="slide c1 r3">
  <div class="abs" style="left:0;width:100%;top:11px;text-align:center;font-size:12.5px">ÜBER UNSERE LEISTUNGEN</div>
  <div class="abs" style="left:0;width:100%;top:27px;text-align:center;font-size:7px">ORIENTIERUNG, STRATEGIE UND UMSETZUNG</div>
  <svg class="abs" style="left:0;top:0" width="368" height="207">
    <circle cx="86" cy="91" r="41" fill="none" stroke="var(--green-mid)" stroke-width="4"/>
    <circle cx="181" cy="91" r="41" fill="none" stroke="var(--green)" stroke-width="4"/>
    <circle cx="281" cy="91" r="41" fill="none" stroke="var(--green-dark)" stroke-width="4"/>
    <circle cx="86" cy="66" r="6" fill="none" stroke="var(--green-mid)" stroke-width="1"/>
    <path d="M83 69 L88 63 L89 64Z" fill="var(--green-mid)"/>
    <path d="M176 61 l3 3 m0 -3 l-3 3 M184 67 l3 3 m0 -3 l-3 3 M179 64 q4 0 5 4" stroke="var(--green)" stroke-width=".9" fill="none"/>
    <circle cx="279" cy="65" r="4" fill="none" stroke="var(--green-dark)" stroke-width="1"/>
    <circle cx="285" cy="69" r="3" fill="none" stroke="var(--green-dark)" stroke-width="1"/>
  </svg>
  <div class="svc" style="left:50px;top:78px"><h5>ORIENTIERUNG</h5><p>Verstehen Sie die rechtlichen Rahmenbedingungen und mögliche Handlungsfelder für Ihr Unternehmen.</p></div>
  <div class="svc" style="left:145px;top:78px"><h5>STRATEGIE</h5><p>Entwickeln Sie eine Nachhaltigkeits&shy;strategie, definieren Sie Ziele und wählen Sie geeignete Maßnahmen aus.</p></div>
  <div class="svc" style="left:245px;top:78px"><h5>UMSETZUNG</h5><p>Verankern Sie die Nachhaltigkeits&shy;strategie wirksam in Ihre Geschäftsprozesse und Unternehmenskultur.</p></div>
  <ul class="tick-list" style="left:58px;top:143px"><li class="lb">LEISTUNGSBEISPIELE:</li><li class="t">Nachhaltigkeits-Kickoff</li><li class="t">Rechts-Kompass</li><li class="t">Status-quo Analyse</li><li class="t">Wettbewerbsanalyse</li></ul>
  <ul class="tick-list" style="left:153px;top:143px"><li class="lb">LEISTUNGSBEISPIELE:</li><li class="t">Stakeholderanalyse</li><li class="t">Wesentlichkeitsanalyse</li><li class="t">Strategieworkshop</li><li class="t">Strategieprozessbegleitung</li></ul>
  <ul class="tick-list" style="left:259px;top:143px"><li class="lb">LEISTUNGSBEISPIELE:</li><li class="t">Mitarbeiterschulung</li><li class="t">Datenerhebung</li><li class="t">Nachhaltigkeitsbericht-erstattung</li><li class="t">Unterstützung bei Ratings &amp;</li><li>&nbsp;&nbsp;Zertifizierungen</li></ul>
  <div class="foot"><span class="url">www.vierklang-beratung.de</span><span class="brand"><i></i>Vierklang</span></div>
</section>

<section class="slide c2 r3">
  <div class="abs" style="left:0;width:100%;top:16px;text-align:center;font-size:8px;color:var(--gold)">WIR VERSTEHEN</div>
  <div class="ucard" style="left:26px"><h4>...die Rolle von<br>Unternehmen als<br>entscheidend</h4><p>Wir sind davon überzeugt, dass echte unternehmerische <b>NACHHALTIGKEIT</b> mit dem Lösen gesellschaftlicher oder ökologischer Probleme einhergeht und somit eine marktwirtschaftliche <b>CHANCE</b> darstellt.</p><span class="pill">Zu unseren Leistungen</span></div>
  <div class="ucard mid" style="left:137px"><h4>...unsere Vision<br>als unseren<br>Antrieb</h4><p>Unsere Vision ist es, gemeinsam mit Ihnen für alle <b>VIER</b> Aspekte der Nachhaltigkeit – Umwelt, Gesellschaft und Wirtschaft – einen <b>MEHRWERT</b> zu erbringen – darum <b>VIERKLANG.</b></p><span class="pill">Zu Über uns</span></div>
  <div class="ucard" style="left:248px"><h4>...es, Sie<br>zukunftsfähig<br>zu machen</h4><p>Wir verstehen die Umsetzung von Nachhaltigkeit als einen multidimensionalen <b>PROZESS,</b> der eine individuelle <b>FOKUSSIERUNG</b> auf das Wesentliche erfordert.</p><span class="pill">Kontaktieren Sie uns</span></div>
  <div class="foot"><span class="url">www.vierklang-beratung.de</span><span class="brand"><i></i>Vierklang</span></div>
</section>

<section class="slide c3 r3">
  <div class="abs" style="left:0;width:100%;top:20px;text-align:center;font-size:21px;color:var(--sand)">ZEITLEISTE</div>
  <svg class="abs" style="left:0;top:0" width="368" height="207">
    <line x1="47" y1="125" x2="321" y2="125" stroke="var(--sand)" stroke-width=".8"/>
    <g transform="translate(47,63)"><path d="M0 56 C-8 44 -21 34 -21 20 A21 21 0 1 1 21 20 C21 34 8 44 0 56Z" fill="#ddd0ac"/><circle cy="20" r="13" fill="none" stroke="#fff" stroke-width="1.3"/><circle cy="62" r="2.5" fill="#ddd0ac"/></g>
    <g transform="translate(117,63)"><path d="M0 56 C-8 44 -21 34 -21 20 A21 21 0 1 1 21 20 C21 34 8 44 0 56Z" fill="#f1dfa3"/><circle cy="20" r="13" fill="none" stroke="#fff" stroke-width="1.3"/><circle cy="62" r="2.5" fill="#f1dfa3"/></g>
    <g transform="translate(184,63)"><path d="M0 56 C-8 44 -21 34 -21 20 A21 21 0 1 1 21 20 C21 34 8 44 0 56Z" fill="#cdbb8a"/><circle cy="20" r="13" fill="none" stroke="#fff" stroke-width="1.3"/><circle cy="62" r="2.5" fill="#cdbb8a"/></g>
    <g transform="translate(254,63)"><path d="M0 56 C-8 44 -21 34 -21 20 A21 21 0 1 1 21 20 C21 34 8 44 0 56Z" fill="#b09147"/><circle cy="20" r="13" fill="none" stroke="#fff" stroke-width="1.3"/><circle cy="62" r="2.5" fill="#b09147"/></g>
    <g transform="translate(321,63)"><path d="M0 56 C-8 44 -21 34 -21 20 A21 21 0 1 1 21 20 C21 34 8 44 0 56Z" fill="#7a5c18"/><circle cy="20" r="13" fill="none" stroke="#fff" stroke-width="1.3"/><circle cy="62" r="2.5" fill="#7a5c18"/></g>
  </svg>
  <div class="tl" style="left:17px"><div class="y">2018</div><div class="h">HEADING</div><div class="d">Lorem Ipsum is simply dummy text</div></div>
  <div class="tl" style="left:87px"><div class="y">2019</div><div class="h">HEADING</div><div class="d">Lorem Ipsum is simply dummy text</div></div>
  <div class="tl" style="left:154px"><div class="y">2020</div><div class="h">HEADING</div><div class="d">Lorem Ipsum is simply dummy text</div></div>
  <div class="tl" style="left:224px"><div class="y">2021</div><div class="h">HEADING</div><div class="d">Lorem Ipsum is simply dummy text</div></div>
  <div class="tl" style="left:291px"><div class="y">2022</div><div class="h">HEADING</div><div class="d">Lorem Ipsum is simply dummy text</div></div>
  <div class="foot"><span class="url">www.vierklang-beratung.de</span><span class="brand"><i></i>Vierklang</span></div>
</section>

<section class="slide c1 r4">
  <div class="dh" style="left:27px;top:37px">HEADING</div>
  <p class="dp" style="left:27px;top:53px">Lorem Ipsum is simply dummy text of the printing and type setting industry.</p>
  <div class="dh" style="left:27px;top:129px">HEADING</div>
  <p class="dp" style="left:27px;top:144px">Lorem Ipsum is simply dummy text of the printing and type setting industry.</p>
  <div class="dh" style="left:252px;top:37px">HEADING</div>
  <p class="dp" style="left:252px;top:53px">Lorem Ipsum is simply dummy text of the printing and type setting industry.</p>
  <div class="dh" style="left:252px;top:127px">HEADING</div>
  <p class="dp" style="left:252px;top:143px">Lorem Ipsum is simply dummy text of the printing and type setting industry.</p>
  <svg class="abs" style="left:112px;top:35px" width="136" height="136" viewBox="-68 -68 136 136">
    <g stroke="#fff" stroke-width="1.5">
      <path d="M0 -68 A68 68 0 0 1 48.08 -48.08 L21.92 -21.92 A31 31 0 0 0 0 -31Z" fill="#d9e46e"/>
      <path d="M48.08 -48.08 A68 68 0 0 1 68 0 L31 0 A31 31 0 0 0 21.92 -21.92Z" fill="#e4ea8c"/>
      <path d="M68 0 A68 68 0 0 1 48.08 48.08 L21.92 21.92 A31 31 0 0 0 31 0Z" fill="#c6df78"/>
      <path d="M48.08 48.08 A68 68 0 0 1 0 68 L0 31 A31 31 0 0 0 21.92 21.92Z" fill="#a9d05c"/>
      <path d="M0 68 A68 68 0 0 1 -48.08 48.08 L-21.92 21.92 A31 31 0 0 0 0 31Z" fill="#f8ebd2"/>
      <path d="M-48.08 48.08 A68 68 0 0 1 -68 0 L-31 0 A31 31 0 0 0 -21.92 21.92Z" fill="#fbe2bd"/>
      <path d="M-68 0 A68 68 0 0 1 -48.08 -48.08 L-21.92 -21.92 A31 31 0 0 0 -31 0Z" fill="#eadbb8"/>
      <path d="M-48.08 -48.08 A68 68 0 0 1 0 -68 L0 -31 A31 31 0 0 0 -21.92 -21.92Z" fill="#e2d2aa"/>
    </g>
    <g font-family="Cabin, sans-serif" font-size="7" fill="#3a2f14" text-anchor="middle">
      <text x="19" y="-44">60%</text><text x="46" y="-17">55%</text><text x="46" y="21">50%</text><text x="19" y="48">45%</text>
      <text x="-19" y="48">40%</text><text x="-46" y="21">35%</text><text x="-46" y="-17">30%</text><text x="-19" y="-44">25%</text>
    </g>
  </svg>
  <div class="foot"><span class="url">www.vierklang-beratung.de</span><span class="brand"><i></i>Vierklang</span></div>
</section>

<section class="slide c2 r4">
  <div class="abs" style="left:21px;top:29px;font-size:18.5px;font-weight:500">THANK YOU</div>
  <div class="abs" style="left:21px;top:65px;font-size:10.5px;color:var(--gold)">VIERKLANG BERATUNG GMBH</div>
  <div class="ct" style="top:87px"><svg width="8" height="8" viewBox="0 0 10 10"><rect x=".5" y=".5" width="9" height="9" rx="2" fill="none" stroke="#c9ab70"/><path d="M3 2.5 Q2.5 6 7 7.5 L7.5 6.3 L6.2 5.6 L5.6 6.2 Q4 5.5 3.8 4.4 L4.4 3.8 L3.8 2.5Z" fill="#c9ab70"/></svg>+49 (0) 6100 – 555 0142</div>
  <div class="ct" style="top:103px"><svg width="8" height="7" viewBox="0 0 10 8"><rect x=".5" y=".5" width="9" height="7" fill="none" stroke="#c9ab70"/><path d="M.5 .5 L5 4.5 L9.5 .5" fill="none" stroke="#c9ab70"/></svg>info@vierklang-beratung.de</div>
  <div class="ct" style="top:119px"><svg width="8" height="10" viewBox="0 0 8 10"><path d="M4 10 C2 7 .5 5.5 .5 3.6 A3.5 3.5 0 0 1 7.5 3.6 C7.5 5.5 6 7 4 10Z" fill="none" stroke="#c9ab70"/><circle cx="4" cy="3.6" r="1.2" fill="#c9ab70"/></svg><span>Lindenhof Bürozentrum<br>Ahornweg 12<br>63000 Musterstadt</span></div>
  <div class="ct" style="top:163px;font-size:8px;line-height:10px;left:20px"><span style="display:block;width:10px;height:10px;background:var(--ink)"></span>Follow Us Netzwerk/vierklang</div>
  <div class="abs" style="left:197px;top:33px;width:140px;height:140px;border-radius:50%;border:2.5px solid var(--green-mid);padding:4px">
    <div role="img" aria-label="Lageplan des Büros" style="width:100%;height:100%;border-radius:50%;background:linear-gradient(135deg,#eef0ee 0%,#e6e9e6 55%,#cfe7d3 100%)"></div>
  </div>
</section>

</body>
</html>
```